Tall Fern Roofing Business Card

Need a business card with the logo that was designed here

Contact Information for Business Card

Name, Title, Phone, Email, Website, Company name

```html
<!DOCTYPE html>
<html lang="en">
<head>
<meta charset="utf-8">
<title>Tall Fern Roofing Business Card</title>
<link href="https://fonts.googleapis.com/css2?family=Poppins:wght@300;400;600;700&display=swap" rel="stylesheet">
<style>
  :root{
    --stage:#2b2624;
    --card:#1c1c1d;
    --blue:#1e78c8;
    --grey:#9a9b9e;
    --white:#f2f2f2;
  }
  html,body{margin:0;padding:0;overflow:hidden;}
  body{width:1200px;height:842px;background:var(--stage);font-family:'Poppins',sans-serif;position:relative;}
  .card{position:absolute;top:251px;width:540px;height:340px;background:var(--card);overflow:hidden;box-shadow:0 14px 30px rgba(0,0,0,.45);}
  .card--contact{left:40px;}
  .card--brand{left:620px;}

  .band{position:absolute;left:0;right:0;}
  .band--top{top:0;height:16px;background:var(--blue);}
  .band--bottom{bottom:0;height:16px;background:var(--grey);}

  .contact{position:absolute;left:0;right:0;top:92px;text-align:center;color:var(--white);}
  .contact__name{margin:0;font-size:25px;font-weight:700;letter-spacing:.5px;line-height:1.1;}
  .contact__first{color:var(--blue);}
  .contact__last{color:var(--grey);}
  .contact__title{margin:2px 0 0;font-size:14px;font-weight:400;letter-spacing:.6px;}
  .rule{display:block;margin:12px auto;width:60px;height:2px;}
  .rule--blue{background:var(--blue);}
  .rule--grey{background:var(--grey);width:64px;height:1px;margin-top:14px;}
  .contact__line{margin:0;font-size:15px;font-weight:300;line-height:1.45;letter-spacing:.4px;}
  .contact__line--phone{font-size:18px;}

  .accent{position:absolute;}
  .accent--left-block{left:0;top:176px;width:38px;height:80px;background:var(--blue);}
  .accent--left-line{left:48px;top:170px;width:4px;height:92px;background:var(--grey);}
  .accent--right-block{right:0;top:46px;width:38px;height:70px;background:var(--blue);}
  .accent--right-line{right:48px;top:40px;width:4px;height:82px;background:var(--grey);}

  .brand{position:absolute;left:0;right:0;top:148px;display:flex;align-items:center;justify-content:center;gap:12px;}
  .brand__mark{width:18px;height:18px;background:var(--blue);}
  .brand__name{margin:0;font-size:30px;font-weight:600;color:var(--blue);letter-spacing:1px;}
</style>
</head>
<body>
  <section class="card card--contact" aria-label="Business card back with contact details">
    <div class="band band--top"></div>
    <div class="contact">
      <h1 class="contact__name"><span class="contact__first">MARCUS</span> <span class="contact__last">HALE</span></h1>
      <p class="contact__title">MANAGING DIRECTOR</p>
      <span class="rule rule--blue"></span>
      <p class="contact__line contact__line--phone">044-987 654 321</p>
      <p class="contact__line">INFO@TALLFERNROOF.COM</p>
      <p class="contact__line">WWW.TALLFERNROOF.COM</p>
      <span class="rule rule--grey"></span>
    </div>
    <div class="band band--bottom"></div>
  </section>

  <section class="card card--brand" aria-label="Business card front with company name">
    <div class="accent accent--left-block"></div>
    <div class="accent accent--left-line"></div>
    <div class="accent accent--right-line"></div>
    <div class="accent accent--right-block"></div>
    <div class="brand">
      <span class="brand__mark"></span>
      <p class="brand__name">Tall Fern Roofing</p>
    </div>
  </section>
</body>
</html>
```